Need a Basketball Court Design

We are replacing our current basketball court (gym floor) and we are looking for a new design. Our team is the “Larkmoor Falcons”. Our mascot is a “Knight” (in shining armor). Our colors are royal blue/grey/black. We are looking for a design that is contemporary and energetic.
The background of the court should display a “castle”. In the center of the court should be a team logo. You can use one of our existing logos or create your own. Along the baseline of the court should read the word “Larkmoor”.
I’ve attached ...
1) a picture of the current court
2) a mock-up design of what we are thinking
3) some of the different team logos we use.

```html
<!DOCTYPE html>
<html lang="en">
<head>
<meta charset="utf-8">
<title>Larkmoor Falcons Basketball Court</title>
<link href="https://fonts.googleapis.com/css2?family=Roboto+Slab:wght@800;900&display=swap" rel="stylesheet">
<style>
  :root {
    --ink: #050505;
    --line: #ffffff;
    --royal: #244c94;
    --wood-light: #ecc996;
    --wood-mid: #e2b47c;
    --wood-dark: #d9a56a;
    --page: #ffffff;
  }
  html, body {
    margin: 0;
    padding: 0;
    width: 1200px;
    height: 600px;
    overflow: hidden;
    background: var(--page);
  }
  .court-design {
    display: block;
    width: 1200px;
    height: 600px;
  }
  .border-band { fill: var(--ink); }
  .floor { fill: url(#wood-tone); }
  .court-line { fill: none; stroke: var(--line); stroke-width: 3; }
  .key-paint { fill: var(--ink); }
  .key-circle-paint { fill: var(--royal); stroke: var(--line); stroke-width: 2; }
  .hoop-line { fill: none; stroke: var(--line); stroke-width: 2.5; }
  .band-text {
    font-family: "Roboto Slab", serif;
    font-weight: 900;
    fill: var(--line);
    font-size: 62px;
  }
  .welcome-text {
    font-family: "Roboto Slab", serif;
    font-weight: 900;
    fill: var(--line);
    font-size: 33px;
  }
  .centre-name {
    font-family: "Roboto Slab", serif;
    font-weight: 900;
    fill: var(--royal);
    font-size: 52px;
  }
  .corner-name {
    font-family: "Roboto Slab", serif;
    font-weight: 900;
    fill: var(--royal);
    font-size: 15px;
  }
  .corner-mark { fill: var(--royal); }
</style>
</head>
<body>
<svg class="court-design" viewBox="0 0 1200 600" xmlns="http://www.w3.org/2000/svg">
  <defs>
    <linearGradient id="wood-tone" x1="0" y1="0" x2="1" y2="1">
      <stop offset="0" stop-color="var(--wood-light)"/>
      <stop offset="0.5" stop-color="var(--wood-mid)"/>
      <stop offset="1" stop-color="var(--wood-dark)"/>
    </linearGradient>
  </defs>

  <rect class="border-band" x="67" y="13" width="1077" height="573"/>

  <rect class="floor" x="135" y="50" width="939" height="498" role="img" aria-label="Maple hardwood floor boards"/>
  <rect class="court-line" x="135" y="50" width="939" height="498"/>
  <line class="court-line" x1="605" y1="50" x2="605" y2="548"/>

  <g class="court-end court-end--left">
    <path class="court-line" d="M135 101 H188 A198 198 0 0 1 188 497 H135"/>
    <rect class="key-paint" x="135" y="238" width="178" height="119"/>
    <path class="key-circle-paint" d="M313 238 A60 59.5 0 0 0 313 357 Z"/>
    <path class="court-line" d="M313 238 A60 59.5 0 0 1 313 357"/>
    <line class="court-line" x1="313" y1="238" x2="313" y2="357"/>
    <g class="hoop-line">
      <line x1="200" y1="231" x2="200" y2="238"/><line x1="228" y1="231" x2="228" y2="238"/>
      <line x1="257" y1="231" x2="257" y2="238"/><line x1="286" y1="231" x2="286" y2="238"/>
      <line x1="200" y1="357" x2="200" y2="364"/><line x1="228" y1="357" x2="228" y2="364"/>
      <line x1="257" y1="357" x2="257" y2="364"/><line x1="286" y1="357" x2="286" y2="364"/>
      <line x1="165" y1="262" x2="165" y2="333"/>
      <line x1="165" y1="297" x2="171" y2="297"/>
      <circle cx="187" cy="297" r="16"/>
    </g>
    <rect class="corner-mark" x="170" y="420" width="14" height="14"/>
    <text class="corner-name" x="190" y="433">LARKMOOR</text>
  </g>

  <g class="court-end court-end--right">
    <path class="court-line" d="M1074 101 H1021 A198 198 0 0 0 1021 497 H1074"/>
    <rect class="key-paint" x="896" y="238" width="178" height="119"/>
    <path class="key-circle-paint" d="M896 238 A60 59.5 0 0 1 896 357 Z"/>
    <path class="court-line" d="M896 238 A60 59.5 0 0 0 896 357"/>
    <line class="court-line" x1="896" y1="238" x2="896" y2="357"/>
    <g class="hoop-line">
      <line x1="923" y1="231" x2="923" y2="238"/><line x1="952" y1="231" x2="952" y2="238"/>
      <line x1="981" y1="231" x2="981" y2="238"/><line x1="1009" y1="231" x2="1009" y2="238"/>
      <line x1="923" y1="357" x2="923" y2="364"/><line x1="952" y1="357" x2="952" y2="364"/>
      <line x1="981" y1="357" x2="981" y2="364"/><line x1="1009" y1="357" x2="1009" y2="364"/>
      <line x1="1044" y1="262" x2="1044" y2="333"/>
      <line x1="1038" y1="297" x2="1044" y2="297"/>
      <circle cx="1018" cy="297" r="16"/>
    </g>
    <rect class="corner-mark" x="950" y="162" width="14" height="14"/>
    <text class="corner-name" x="970" y="175">LARKMOOR</text>
  </g>

  <text class="centre-name" x="605" y="316" text-anchor="middle">LARKMOOR</text>

  <text class="band-text" transform="translate(124 440) rotate(-90)" textLength="295" lengthAdjust="spacing">FALCONS</text>
  <text class="band-text" transform="translate(1085 75) rotate(90)" textLength="438" lengthAdjust="spacing">BASKETBALL</text>
  <text class="welcome-text" x="323" y="580" textLength="585" lengthAdjust="spacing">WELCOME TO THE FALCON NEST</text>
</svg>
</body>
</html>
```